Quillbrookes websites redesign

Www.quill-brookes.com needs to be redesigned along with updations. The incremental material will be provided for the updations. We are looking for complete redesign of the pages with the new content. The complete write up will be provided soon

Target Market(s)

Global

Coding

Coded - Design and coding required

Number of Pages Required

5+ page

Requirements
Must have
• A clean and slick design for the Consulting.
Should not have
• Too many pictures which reduces the speed of the site

```html
<!DOCTYPE html>
<html lang="en">
<head>
<meta charset="utf-8">
<title>Quillbrookes – Trade Finance Consultancy</title>
<link href="https://fonts.googleapis.com/css2?family=Open+Sans:ital,wght@0,400;0,600;0,700;1,600&family=Raleway:wght@500;600;700&display=swap" rel="stylesheet">
<style>
:root{
  --blue:#2e9bc6;
  --blue-dark:#0d3f7a;
  --blue-deep:#06264f;
  --maroon:#5b1a1f;
  --ink:#222;
  --text:#777;
  --pale:#eef4f6;
  --white:#fff;
  --footer:#242424;
  --footer-text:#c9c9c9;
  --map:#8fcdf7;
}
*{box-sizing:border-box;margin:0;padding:0}
html,body{width:1200px;height:2894px;overflow:hidden}
body{position:relative;font-family:"Open Sans",Arial,sans-serif;color:var(--ink);background:var(--white)}
.abs{position:absolute}

/* header */
.site-header{position:absolute;left:0;top:0;width:1200px;height:90px;background:var(--white);border-top:5px solid var(--blue)}
.brand{position:absolute;left:96px;top:26px;display:flex;align-items:center;gap:10px}
.brand-dot{width:38px;height:38px;border-radius:50%;background:var(--blue)}
.brand-name{font-family:"Open Sans",Arial,sans-serif;font-weight:600;font-size:31px;color:var(--maroon)}
.main-nav{position:absolute;left:478px;top:36px;display:flex;gap:0}
.main-nav a{font-family:"Open Sans",Arial,sans-serif;font-size:15px;color:#222;text-decoration:none;margin-right:34px}
.main-nav a.active{color:var(--blue)}
.search-btn{position:absolute;left:1062px;top:23px;width:40px;height:40px;border-radius:50%;background:var(--maroon);display:flex;align-items:center;justify-content:center}

/* hero */
.hero{position:absolute;left:0;top:90px;width:1200px;height:435px;
  background:radial-gradient(ellipse at 50% 30%,#7fd2f7 0%,#2f9de0 25%,#1163b4 55%,var(--blue-deep) 100%)}
.hero-title{position:absolute;left:0;width:1200px;top:68px;text-align:center;font-family:"Raleway",sans-serif;font-weight:600;font-size:60px;color:var(--white);text-shadow:0 2px 6px rgba(0,0,0,.35)}
.hero-sub{position:absolute;left:0;width:1200px;top:306px;text-align:center;font-family:"Raleway",sans-serif;font-weight:700;font-size:21px;color:var(--white)}
.hero-arrow{position:absolute;top:202px}
.stats{position:absolute;top:453px;left:0;width:1200px;height:120px}
.stat{position:absolute;top:0;width:122px;height:122px;border-radius:50%;background:var(--white);border:6px solid var(--blue);border-top-color:#d8ecf4;border-right-color:#d8ecf4;
  display:flex;align-items:center;justify-content:center;font-family:"Raleway",sans-serif;font-weight:700;font-size:21px;color:#111;box-shadow:0 2px 6px rgba(0,0,0,.12)}

/* founder */
.founder{position:absolute;left:0;top:525px;width:1200px;height:450px;background:var(--pale)}
.founder-photo{position:absolute;left:100px;top:98px;width:300px;height:311px;border:6px solid var(--white);box-shadow:0 1px 4px rgba(0,0,0,.15);
  background:linear-gradient(160deg,#b9424c 0%,#8d1c2a 45%,#d9863a 100%)}
.founder-name{position:absolute;left:451px;top:98px;font-family:"Raleway",sans-serif;font-weight:700;font-size:21px;color:#222}
.founder-bio{position:absolute;left:451px;top:145px;width:652px;font-size:12.5px;line-height:24px;color:var(--text)}
.founder-bio p+p{margin-top:24px}
.read-more{font-family:"Open Sans",Arial,sans-serif;font-weight:700;font-size:12.5px;color:var(--maroon);text-decoration:none}

/* section heads */
.section-title{position:absolute;left:0;width:1200px;text-align:center;font-family:"Raleway",sans-serif;font-weight:700;font-size:22px;color:#222}

/* consultancy */
.consultancy{position:absolute;left:0;top:975px;width:1200px;height:517px;background:var(--white)}
.service{position:absolute;top:98px;width:313px}
.service-photo{width:313px;height:225px;border:5px solid #f0f0f0;box-shadow:0 0 0 1px #e2e2e2}
.service h3{margin-top:31px;font-family:"Open Sans",Arial,sans-serif;font-weight:700;font-size:15px;color:#222}
.service p{margin-top:10px;font-size:12px;line-height:23px;color:var(--text)}
.service .read-more{display:block;margin-top:10px}

/* platform */
.platform{position:absolute;left:0;top:1492px;width:1200px;height:437px;background:var(--pale)}
.platform-intro{position:absolute;left:140px;top:88px;width:920px;text-align:center;font-size:12px;line-height:27px;color:var(--text)}
.step{position:absolute;top:188px;width:180px;text-align:center}
.step-ring{margin:0 auto;width:114px;height:114px;border-radius:50%;border:3px solid var(--blue);background:var(--white);display:flex;align-items:center;justify-content:center}
.step-core{width:98px;height:98px;border-radius:50%;background:var(--blue);display:flex;align-items:center;justify-content:center}
.step-label{margin-top:24px;font-family:"Open Sans",Arial,sans-serif;font-weight:600;font-size:15px;line-height:20px;color:#222}

/* case studies */
.cases{position:absolute;left:0;top:1929px;width:1200px;height:631px;background:var(--white)}
.cases-sub{position:absolute;left:0;width:1200px;top:76px;text-align:center;font-family:"Open Sans",Arial,sans-serif;font-style:italic;font-weight:600;font-size:16px;color:var(--blue)}
.map-frame{position:absolute;left:154px;top:116px;width:892px;height:453px;border:1px solid #dcdcdc;background:var(--white);padding:30px 40px}
.map-fill{width:100%;height:100%;border-radius:40px;background:radial-gradient(ellipse at 50% 45%,var(--map) 0%,#b5ddf8 60%,#e8f5fd 100%)}

/* footer */
.site-footer{position:absolute;left:0;top:2560px;width:1200px;height:334px;background:var(--footer);color:var(--footer-text)}
.footer-col{position:absolute;top:34px}
.footer-col h4{font-family:"Open Sans",Arial,sans-serif;font-weight:700;font-size:15px;color:var(--white);text-transform:uppercase;letter-spacing:.2px}
.footer-links{list-style:none;margin-top:16px}
.footer-links li{font-size:12px;line-height:25px;color:var(--footer-text)}
.col-divider{position:absolute;top:34px;width:1px;height:200px;background:#3a3a3a}
.newsletter p{margin-top:16px;width:290px;font-size:12px;line-height:22px}
.email-field{margin-top:20px;width:300px;height:32px;background:var(--white);font-size:11.5px;color:#999;padding:8px 14px}
.subscribe{margin-top:29px;width:98px;height:36px;background:var(--blue);border:2px solid var(--white);border-radius:3px;color:var(--white);font-weight:700;font-size:11px;display:flex;align-items:center;justify-content:center;letter-spacing:.3px}
.contact-list{list-style:none;margin-top:18px}
.contact-list li{display:flex;gap:16px;font-size:12px;line-height:19px;margin-bottom:12px;width:240px}
.contact-list svg{flex:none;margin-top:2px}
.footer-rule{position:absolute;left:98px;top:247px;width:1004px;height:1px;background:#3a3a3a}
.footer-brand{position:absolute;left:98px;top:270px;display:flex;align-items:center;gap:9px}
.footer-brand .brand-dot{width:32px;height:32px;background:var(--white)}
.footer-brand .brand-name{color:var(--white);font-size:25px}
.copyright{position:absolute;left:443px;top:282px;font-size:12px;color:var(--footer-text)}
.social{position:absolute;left:933px;top:270px;display:flex;gap:8px}
.social span{width:38px;height:38px;border-radius:50%;border:2px solid var(--white)}
</style>
</head>
<body>

<header class="site-header">
  <div class="brand"><span class="brand-dot"></span><span class="brand-name">Quillbrookes</span></div>
  <nav class="main-nav">
    <a class="active" href="#">Home</a><a href="#">Founder</a><a href="#">Consultancy</a><a href="#">Platform</a><a href="#">Case Studies</a><a href="#">Contact Us</a>
  </nav>
  <div class="search-btn">
    <svg width="18" height="18" viewBox="0 0 18 18"><circle cx="7.5" cy="7.5" r="5.5" fill="none" stroke="#fff" stroke-width="2.4"/><line x1="11.5" y1="11.5" x2="16" y2="16" stroke="#fff" stroke-width="2.6" stroke-linecap="round"/></svg>
  </div>
</header>

<section class="hero" role="img" aria-label="Globe above a crowd of business silhouettes linked by a glowing network on blue">
  <h1 class="hero-title">Global Trade Forum</h1>
  <p class="hero-sub">World Merchandising Trade 2012 ( USD Billion)</p>
  <svg class="hero-arrow" style="left:44px" width="16" height="26" viewBox="0 0 16 26"><polyline points="13,2 3,13 13,24" fill="none" stroke="#fff" stroke-width="3"/></svg>
  <svg class="hero-arrow" style="left:1140px" width="16" height="26" viewBox="0 0 16 26"><polyline points="3,2 13,13 3,24" fill="none" stroke="#fff" stroke-width="3"/></svg>
</section>

<section class="founder">
  <div class="founder-photo" role="img" aria-label="Founder speaking at a podium with flowers in front"></div>
  <h2 class="founder-name">Maya Ranganathan</h2>
  <div class="founder-bio">
    <p>Ms. Maya Ranganathan is the founder director of Quillbrookes Consultancy Limited (QCL) based at Hong Kong. Maya worked as the Alternate Chief Executive of Northbay Bank, Hong Kong Branch until Jan 2013, heading Corporate Banking business in North Asia and Export Credit Agency business globally. During her tenure, both the businesses increased multifold.</p>
    <p>Maya started her banking career with Northbay Bank Ltd, one of India's largest banks, in the year 2002 and in the next 10 years handled multiple leadership responsibilities in the Corporate, Institutional and International Banking space across India, North Asia, Americas and Europe.</p>
    <p><a class="read-more" href="#">READ MORE &gt;&gt;</a></p>
  </div>
</section>

<div class="stats">
  <div class="stat" style="left:165px">0 - 250</div>
  <div class="stat" style="left:412px">250 - 500</div>
  <div class="stat" style="left:662px">500 - 1000</div>
  <div class="stat" style="left:913px">&gt; 1000</div>
</div>

<section class="consultancy">
  <h2 class="section-title" style="top:40px">Consultancy</h2>
  <article class="service" style="left:98px">
    <div class="service-photo" role="img" aria-label="Hand with pen over financial charts" style="background:linear-gradient(135deg,#e9ecef,#8b96a4 60%,#2b3440)"></div>
    <h3>Bank Consultancy</h3>
    <p>Capacity Building for Trade Finance either through Export Credit Insurance/Developmental Financial Institution and Private Risk.</p>
    <a class="read-more" href="#">READ MORE &gt;&gt;</a>
  </article>
  <article class="service" style="left:443px">
    <div class="service-photo" role="img" aria-label="Hands reviewing documents at a desk" style="background:linear-gradient(135deg,#f6f1ea,#d7c3ae 55%,#5f86a8)"></div>
    <h3>Corporate Consultancy: ( Plain Vanilla )</h3>
    <p>Capacity Building for Trade Finance either through Export Credit Insurance/Developmental Financial Institution and Private Risk.</p>
    <a class="read-more" href="#">READ MORE &gt;&gt;</a>
  </article>
  <article class="service" style="left:787px">
    <div class="service-photo" role="img" aria-label="Business meeting in front of a glowing world map screen" style="background:linear-gradient(160deg,#9bb4cc,#4f6f8e 50%,#e9eef2)"></div>
    <h3>Corporate Consultancy: ( Structured )</h3>
    <p>Capacity Building for Trade Finance either through Export Credit Insurance/Developmental Financial Institution and Private Risk.</p>
    <a class="read-more" href="#">READ MORE &gt;&gt;</a>
  </article>
</section>

<section class="platform">
  <h2 class="section-title" style="top:38px">Platform</h2>
  <p class="platform-intro">Quillbrookes Consultancy Limited also works with corporates and banks to increase transactional efficiency of trade finance. For this objective, it owns B2B Cross Border Trade Finance Platform which is a marketplace matching trade flows with global trade finance capacities for corporates and financial institutions.</p>

  <svg class="abs" style="left:0;top:160px" width="1200" height="140" viewBox="0 0 1200 140">
    <g fill="none" stroke="#d3d3d3" stroke-width="5">
      <path d="M205 35 Q245 5 285 30"/><path d="M384 120 Q425 150 462 118"/>
      <path d="M562 35 Q602 5 642 30"/><path d="M742 120 Q782 150 820 118"/>
      <path d="M920 35 Q958 5 998 30"/>
    </g>
    <g fill="#d3d3d3">
      <polygon points="285,22 293,36 279,36"/><polygon points="462,108 470,122 456,124"/>
      <polygon points="642,22 650,36 636,36"/><polygon points="820,108 828,122 814,124"/>
      <polygon points="998,22 1006,36 992,36"/>
    </g>
  </svg>

  <div class="step" style="left:64px"><div class="step-ring"><div class="step-core">
    <svg width="40" height="44" viewBox="0 0 40 44" fill="none" stroke="#fff" stroke-width="2.6"><path d="M6 3h20l8 8v30H6z"/><path d="M26 3v8h8"/><line x1="12" y1="20" x2="28" y2="20"/><line x1="12" y1="27" x2="28" y2="27"/><line x1="12" y1="34" x2="24" y2="34"/></svg>
  </div></div><div class="step-label">Register<br>on the website</div></div>

  <div class="step" style="left:242px"><div class="step-ring"><div class="step-core">
    <svg width="42" height="42" viewBox="0 0 42 42" fill="none" stroke="#fff" stroke-width="2.6"><rect x="4" y="8" width="28" height="30" rx="3"/><path d="M16 27l2-7 16-16 5 5-16 16z" fill="#2e9bc6"/></svg>
  </div></div><div class="step-label" style="margin-top:34px">Input Deal</div></div>

  <div class="step" style="left:419px"><div class="step-ring"><div class="step-core">
    <svg width="40" height="34" viewBox="0 0 40 34" fill="#fff"><path d="M2 16h12v16H2zM2 16Q2 4 14 2v5Q7 8 7 16z"/><path d="M22 16h12v16H22zM22 16Q22 4 34 2v5Q27 8 27 16z"/></svg>
  </div></div><div class="step-label">Quotes Submitted<br>from around the<br>world</div></div>

  <div class="step" style="left:599px"><div class="step-ring"><div class="step-core">
    <svg width="42" height="40" viewBox="0 0 42 40" fill="none" stroke="#fff" stroke-width="3"><rect x="4" y="6" width="30" height="30" rx="4"/><polyline points="11,20 18,27 38,6"/></svg>
  </div></div><div class="step-label">Best<br>quotes selection</div></div>

  <div class="step" style="left:776px"><div class="step-ring"><div class="step-core">
    <svg width="40" height="40" viewBox="0 0 40 40" fill="#fff"><rect x="3" y="17" width="8" height="20" rx="1"/><path d="M14 18l8-14c3 0 5 2 4 6l-2 6h10c3 0 4 3 3 5l-4 13c-1 2-2 3-4 3H14z"/></svg>
  </div></div><div class="step-label" style="margin-top:34px">Deal Matching</div></div>

  <div class="step" style="left:956px"><div class="step-ring"><div class="step-core">
    <svg width="42" height="40" viewBox="0 0 42 40" fill="#fff"><path d="M40 2L2 18l12 5 3 13 6-8 9 7z"/><path d="M14 23L36 7 18 26z" fill="#2e9bc6"/></svg>
  </div></div><div class="step-label">Support<br>in Execution</div></div>
</section>

<section class="cases">
  <h2 class="section-title" style="top:36px">Case Studies</h2>
  <p class="cases-sub">Geographical Reach –Corporate Deals Placed</p>
  <div class="map-frame">
    <div class="map-fill" role="img" aria-label="World map with pins marking corporate deals placed in North America, Europe, Kuwait, Dubai, Hong Kong and Singapore"></div>
  </div>
</section>

<footer class="site-footer">
  <div class="footer-col" style="left:98px">
    <h4>Information</h4>
    <ul class="footer-links"><li>Home</li><li>Founder</li><li>Consultancy</li><li>System</li><li>Case Studies</li><li>Contact Us</li></ul>
  </div>
  <div class="col-divider" style="left:250px"></div>
  <div class="footer-col newsletter" style="left:286px">
    <h4>Newsletter Subscription</h4>
    <p>Register your email address to get information about us</p>
    <div class="email-field">Email Address</div>
    <div class="subscribe">SUBSCRIBE</div>
  </div>
  <div class="col-divider" style="left:630px"></div>
  <div class="footer-col" style="left:681px">
    <h4>Quick Links</h4>
    <ul class="footer-links"><li>Query</li><li>Help</li><li>FAQ</li><li>Privacy Policy</li><li>Terms &amp; Conditions</li><li>System</li></ul>
  </div>
  <div class="col-divider" style="left:840px"></div>
  <div class="footer-col" style="left:878px">
    <h4>Contact Us</h4>
    <ul class="contact-list">
      <li><svg width="12" height="16" viewBox="0 0 12 16"><path d="M6 0a6 6 0 0 1 6 6c0 4-6 10-6 10S0 10 0 6a6 6 0 0 1 6-6z" fill="#fff"/><circle cx="6" cy="6" r="2.2" fill="#242424"/></svg><span>Unit 01, 12th Floor, Harbour Point Centre, 8 Lantern Road, Kowloon, Hong Kong</span></li>
      <li><svg width="13" height="14" viewBox="0 0 13 14"><path d="M2 0l3 3-1.5 2.5c1 2 2.5 3.5 4.5 4.5L10.5 8.5 13 11.5 11 14C5 13 0 8 0 2z" fill="#fff"/></svg><span>+852-2000-4178</span></li>
      <li><svg width="14" height="14" viewBox="0 0 14 14"><rect x="0" y="4" width="14" height="9" rx="1" fill="#fff"/><rect x="3" y="0" width="8" height="5" fill="#fff"/><rect x="3" y="7" width="8" height="2" fill="#242424"/></svg><span>+852-2000-4190</span></li>
      <li><svg width="14" height="11" viewBox="0 0 14 11"><rect width="14" height="11" rx="1" fill="#fff"/><polyline points="1,1 7,6 13,1" fill="none" stroke="#242424" stroke-width="1.4"/></svg><span>query@quill-brookes.com</span></li>
    </ul>
  </div>
  <div class="footer-rule"></div>
  <div class="footer-brand"><span class="brand-dot"></span><span class="brand-name">Quillbrookes</span></div>
  <p class="copyright">Copyrights © 2016, Quillbrookes. All rights reserved.</p>
  <div class="social"><span></span><span></span><span></span><span></span></div>
</footer>

</body>
</html>
```